Beacon Advisory Website

I currently have a website www.beaconadvisoryinc.com. We are a IT Consulting Company. Our website will pretty much tell out our services. I am looking to enhance my website and make it look more professional. Looking for very classy and Contemporary look and design for my website.

It Company

```html
<!DOCTYPE html>
<html lang="en">
<head>
<meta charset="utf-8">
<title>Beacon Advisory</title>
<link href="https://fonts.googleapis.com/css2?family=Raleway:wght@400;500;600;700&family=Open+Sans:ital,wght@0,400;0,600;0,700;1,400&display=swap" rel="stylesheet">
<style>
:root{
  --blue:#1aa3dc;
  --blue-bright:#12a8e6;
  --navy:#1a5ea6;
  --navy-deep:#174f8c;
  --ink:#2b2b2b;
  --muted:#5e5e5e;
  --grey-band:#e8ecf0;
  --white:#ffffff;
}
*{box-sizing:border-box;margin:0;padding:0}
html,body{width:672px;height:1200px;overflow:hidden;background:var(--white)}
body{position:relative;font-family:"Open Sans",Arial,sans-serif;color:var(--ink)}
.abs{position:absolute}

/* header */
.site-header{left:0;top:0;width:672px;height:50px;background:linear-gradient(#fafbfc,#eceff2);border-top:2px solid var(--blue)}
.brand{left:60px;top:12px;display:flex;align-items:center;gap:6px}
.brand-mark{width:20px;height:20px;border-radius:50%;background:var(--navy)}
.brand-name{font-family:"Raleway",sans-serif;font-weight:700;font-size:15px;color:var(--navy);letter-spacing:.2px}
.contact-chip{top:14px;display:flex;gap:7px;align-items:center}
.chip-icon{width:19px;height:19px;border-radius:50%;background:var(--navy);display:flex;align-items:center;justify-content:center}
.chip-label{font-size:7px;font-weight:700;color:var(--navy);line-height:1.1}
.chip-value{font-size:8px;color:#444}

/* nav */
.main-nav{left:0;top:50px;width:672px;height:24px;background:linear-gradient(#1a8cd0,#1266a8);display:flex;padding-left:60px}
.main-nav a{font-size:7.5px;font-weight:700;color:var(--white);text-decoration:none;height:24px;line-height:24px;text-align:center;border-right:1px solid rgba(255,255,255,.12)}
.main-nav a.active{background:var(--blue-bright)}

/* hero */
.hero{left:0;top:74px;width:672px;height:228px;background:radial-gradient(circle at 70% 45%,#2d6ea8 0%,#163a62 45%,#0c1c33 100%)}
.hero-title{left:60px;top:144px;width:270px;font-family:"Raleway",sans-serif;font-weight:700;font-size:14px;line-height:18.5px;color:var(--white)}
.btn-more{left:60px;top:213px;width:68px;height:22px;background:var(--blue-bright);color:var(--white);font-size:7px;font-weight:700;display:flex;align-items:center;justify-content:center}

/* welcome */
.welcome{left:0;top:302px;width:672px;height:108px;background:var(--blue)}
.welcome h1{position:absolute;left:0;top:11px;width:672px;text-align:center;font-family:"Raleway",sans-serif;font-weight:400;font-size:17.5px;color:var(--white)}
.welcome-rule{left:186px;top:37px;width:300px;height:1px;background:rgba(255,255,255,.5)}
.welcome p{position:absolute;left:64px;top:50px;width:544px;text-align:center;font-size:7.1px;line-height:12px;color:#e6f5fc}
.expand{left:324px;top:93px;width:24px;height:15px;background:#3b3b3b;border-radius:3px 3px 0 0;color:#fff;font-size:13px;line-height:15px;text-align:center;font-weight:700}

/* features */
.feature{top:436px;width:190px;text-align:center}
.feature svg{display:block;margin:0 auto}
.feature h3{margin-top:12px;font-size:9.5px;font-weight:700;color:var(--ink)}
.feature.highlight h3{color:var(--blue-bright)}
.feature p{margin-top:4px;font-size:7px;line-height:9.5px;color:var(--muted);padding:0 12px}

/* services */
.services{left:0;top:608px;width:672px;height:180px;background:var(--grey-band)}
.section-title{position:absolute;left:0;width:672px;text-align:center;font-family:"Raleway",sans-serif;font-weight:400;font-size:17.5px;color:var(--ink)}
.section-title span{color:var(--blue-bright)}
.section-rule{width:170px;height:1px;left:251px;background:#c4c9ce}
.rule-dot{width:8px;height:8px;left:332px;border-radius:2px;background:var(--navy)}
.service-card{top:62px;width:165px;height:94px}
.card-photo{position:absolute;inset:0}
.card-caption{position:absolute;left:0;bottom:0;width:100%;height:19px;background:rgba(23,79,140,.85);color:#fff;font-family:"Raleway",sans-serif;font-size:10px;text-align:center;line-height:19px}
.card-overlay{position:absolute;inset:0;background:#1f5fa0;color:#fff;text-align:center;padding:14px 10px 0}
.card-overlay h4{font-size:10px;font-weight:700}
.card-overlay p{font-size:6.3px;line-height:9.5px;margin-top:5px;font-weight:600}
.card-overlay .link{font-size:6px;font-weight:700;margin-top:5px}

/* testimonial */
.avatar{left:70px;top:858px;width:80px;height:80px;border-radius:50%;border:3px solid #d4d4d4;background:radial-gradient(circle at 50% 40%,#c9ccd1,#7a8290)}
.quote-text{left:166px;top:853px;width:444px;font-size:7.2px;line-height:13.5px;font-style:italic;color:var(--muted);text-align:center}
.quote-rule{left:166px;top:920px;width:444px;height:1px;background:#e2e2e2}
.quote-author{left:222px;top:928px;font-size:7.5px;font-weight:700;color:var(--navy)}
.pager{left:523px;top:931px;display:flex;gap:3px}
.pager i{width:5px;height:5px;border-radius:50%;background:#c9c9c9;display:block}
.pager i.on{background:var(--blue-bright)}

/* footer */
.footer-wave{left:0;top:920px;width:672px;height:90px}
.site-footer{left:0;top:1008px;width:672px;height:167px;background:var(--navy)}
.f-col{top:1029px}
.f-col h5{font-family:"Raleway",sans-serif;font-size:10px;font-weight:600;color:#fff;margin-bottom:10px}
.f-links li{list-style:none;font-size:6.5px;color:#e3eefa;margin-bottom:13px;display:flex;align-items:center;gap:6px}
.f-links li::before{content:"";width:2.5px;height:2.5px;background:#fff;border-radius:50%}
.f-info{font-size:6.5px;color:#e3eefa;line-height:9px}
.f-info .row{display:flex;gap:8px;margin-bottom:11px}
.f-info svg{flex:none;margin-top:1px}
.divider{top:1030px;width:1px;height:130px;background:rgba(0,0,0,.15)}
.field{width:150px;border:1px solid rgba(255,255,255,.6);color:#dfeaf7;font-size:6.5px;padding:4px 6px;margin-bottom:5px}
.submit{width:58px;height:18px;background:linear-gradient(#fff,#d9d9d9);border-radius:2px;color:#333;font-size:7px;text-align:center;line-height:18px}
.f-brand{left:500px;top:1064px;display:flex;align-items:center;gap:5px}
.f-brand .brand-mark{background:#fff}
.f-brand .brand-name{color:#fff;font-size:13px}
.socials{left:504px;top:1114px;display:flex;gap:8px}
.socials i{display:block;width:17px;height:17px;background:#2b8fd6;border:1px solid rgba(255,255,255,.3)}
.copyright{left:0;top:1175px;width:672px;height:25px;background:var(--navy-deep);color:#d8e4f2;font-size:6.5px;text-align:center;line-height:25px}
</style>
</head>
<body>

<header class="abs site-header">
  <div class="abs brand">
    <span class="brand-mark"></span><span class="brand-name">Beacon Advisory</span>
  </div>
  <div class="abs contact-chip" style="left:374px">
    <span class="chip-icon"><svg width="9" height="9" viewBox="0 0 10 10"><rect x="3" y="1" width="4" height="8" rx="1" fill="#fff"/></svg></span>
    <div><div class="chip-label">CALL US</div><div class="chip-value">+1 (555) 014 2290</div></div>
  </div>
  <div class="abs contact-chip" style="left:475px">
    <span class="chip-icon"><svg width="9" height="9" viewBox="0 0 10 10"><rect x="1" y="2.5" width="8" height="5.5" fill="none" stroke="#fff" stroke-width="1"/><polyline points="1,2.5 5,6 9,2.5" fill="none" stroke="#fff" stroke-width="1"/></svg></span>
    <div><div class="chip-label">EMAIL US</div><div class="chip-value">info@beaconadvisoryinc.com</div></div>
  </div>
</header>

<nav class="abs main-nav">
  <a class="active" style="width:62px">HOME</a>
  <a style="width:85px">ABOUT US</a>
  <a style="width:78px">SERVICES</a>
  <a style="width:84px">SOLUTIONS</a>
  <a style="width:86px">RESOURCES</a>
  <a style="width:71px">CAREER</a>
  <a style="width:90px;border:none">CONTACT US</a>
</nav>

<section class="abs hero" role="img" aria-label="Hand in a suit touching a glowing digital gear network"></section>
<h2 class="abs hero-title">We Will Delivers Highest Level Of Quality Consultants And Services For The Lowest Cost Of Ownership</h2>
<div class="abs btn-more">READ MORE</div>

<section class="abs welcome">
  <h1>Welcome To Beacon Advisoryinc</h1>
  <div class="abs welcome-rule"></div>
  <svg class="abs" style="left:330px;top:35px" width="12" height="6"><polygon points="0,0 12,0 6,6" fill="#fff"/></svg>
  <p>Today's IT market is a dynamic, fast-paced industry, with ever-increasing demands. Meeting these demands for over 25 years, Beacon Advisory maintains a global presence, aggressively recruiting expertly qualified IT and Management Professionals from around the world and cultivating key partnerships with corporations to understand their business models end-to-end, with a goal of delivering exceptional client service and ensuring a consistent delivery....</p>
  <div class="abs expand">+</div>
</section>

<div class="abs feature" style="left:54px">
  <svg width="90" height="90" viewBox="0 0 90 90">
    <g fill="none" stroke="#555" stroke-width="1"><polyline points="36,9 45,1 54,9"/><polyline points="36,81 45,89 54,81"/><polyline points="9,36 1,45 9,54"/><polyline points="81,36 89,45 81,54"/></g>
    <g fill="#2b2b2b"><circle cx="37" cy="36" r="3.5"/><circle cx="53" cy="36" r="3.5"/><rect x="31" y="41" width="28" height="5"/><rect x="33" y="47" width="8" height="9"/><rect x="49" y="47" width="8" height="9"/></g>
  </svg>
  <h3>CONSULTING</h3>
  <p>Beacon Advisory has certified professional consultants to work with you to help increase the business by providing IT services ...</p>
</div>

<div class="abs feature highlight" style="left:249px">
  <svg width="90" height="90" viewBox="0 0 90 90">
    <g fill="none" stroke="#1aa3dc" stroke-width="1"><polyline points="36,1 45,9 54,1"/><polyline points="36,89 45,81 54,89"/><polyline points="1,36 9,45 1,54"/><polyline points="89,36 81,45 89,54"/></g>
    <g fill="#1aa3dc"><circle cx="45" cy="45" r="9"/><g stroke="#1aa3dc" stroke-width="4"><line x1="45" y1="33" x2="45" y2="57"/><line x1="33" y1="45" x2="57" y2="45"/><line x1="36.5" y1="36.5" x2="53.5" y2="53.5"/><line x1="53.5" y1="36.5" x2="36.5" y2="53.5"/></g></g>
    <circle cx="45" cy="45" r="3.5" fill="#fff"/>
  </svg>
  <h3>STAFF AUGMENTATION</h3>
  <p>For years Beacon Advisory as been offering our customers the ability to augment their existing staff..</p>
</div>

<div class="abs feature" style="left:432px">
  <svg width="90" height="90" viewBox="0 0 90 90">
    <g fill="none" stroke="#555" stroke-width="1"><polyline points="36,9 45,1 54,9"/><polyline points="36,81 45,89 54,81"/><polyline points="9,36 1,45 9,54"/><polyline points="81,36 89,45 81,54"/></g>
    <rect x="34" y="34" width="22" height="22" rx="4" fill="#2b2b2b"/>
  </svg>
  <h3>OFFSHORE</h3>
  <p>Our Offshore development model has a unique distinction of providing efficient software solutions ...</p>
</div>

<section class="abs services">
  <h2 class="section-title" style="top:12px">Our <span>Services</span></h2>
  <div class="abs section-rule" style="top:38px"></div>
  <div class="abs rule-dot" style="top:35px"></div>
  <svg class="abs" style="left:28px;top:92px" width="16" height="30"><polyline points="15,1 1,15 15,29" fill="none" stroke="#8a8a8a" stroke-width="1"/></svg>
  <svg class="abs" style="left:626px;top:92px" width="16" height="30"><polyline points="1,1 15,15 1,29" fill="none" stroke="#8a8a8a" stroke-width="1"/></svg>

  <div class="abs service-card" style="left:60px">
    <div class="card-photo" role="img" aria-label="Businessman touching a holographic technology icon network" style="background:radial-gradient(circle at 50% 40%,#5a6f88,#1c2838)"></div>
    <div class="card-caption">Technology</div>
  </div>
  <div class="abs service-card" style="left:253px">
    <div class="card-overlay">
      <h4>OFFSHORE</h4>
      <p>Our Offshore development model has a unique distinction of providing efficient software solutions with cost and quality advantage, using state-of-the-art</p>
      <div class="link">READ MORE »</div>
    </div>
  </div>
  <div class="abs service-card" style="left:447px">
    <div class="card-photo" role="img" aria-label="Person selecting floating application icons on a blue screen" style="background:radial-gradient(circle at 40% 40%,#8ec4e8,#2a6aa4)"></div>
    <div class="card-caption">Application Developement</div>
  </div>
</section>

<h2 class="section-title" style="top:806px">Client <span>Testimonial</span></h2>
<div class="abs section-rule" style="top:833px"></div>
<div class="abs rule-dot" style="top:830px"></div>

<div class="abs avatar" role="img" aria-label="Portrait photo of the client"></div>
<p class="abs quote-text">“ Lorem ipsum dolor sit amet, consectetuer adipiscing elit, sed diam nonummy nibh euismod tincidunt utvm laoreetm dolore magna aliquam erat volutpat. Ut wisi enim ad minim veniam, quis nostrud exerci tation ullamcorper suscipit lobortis nisl utmv aliquip ex ea commodo consequat. Duis autem vel eum iriure dolor in hendrerit in vulputate velit esse molestie consequat, velm illu dolore eu feugiat nulla facilisis at vero eros et accumsan etsto duis facilisi. ”</p>
<div class="abs quote-rule"></div>
<div class="abs quote-author">- Miss Clara Penn</div>
<div class="abs pager"><i class="on"></i><i></i><i></i><i></i></div>

<svg class="abs footer-wave" viewBox="0 0 672 90" preserveAspectRatio="none">
  <path d="M0 84 C120 40 250 58 380 80 C500 100 600 62 672 16 L672 90 L0 90Z" fill="#1a5ea6"/>
  <path d="M270 60 C420 98 560 84 672 8 L672 24 C580 90 430 104 270 60Z" fill="#12a8e6"/>
</svg>

<footer class="abs site-footer"></footer>

<div class="abs f-col" style="left:59px">
  <h5>Quick Links</h5>
  <ul class="f-links"><li>Home</li><li>About Us</li><li>Services</li><li>Resources</li><li>Contact Us</li></ul>
</div>
<div class="abs divider" style="left:133px"></div>

<div class="abs f-col f-info" style="left:159px">
  <h5>Contact Information</h5>
  <div class="row"><svg width="7" height="9" viewBox="0 0 7 9"><path d="M3.5 0A3.5 3.5 0 0 0 0 3.5C0 6 3.5 9 3.5 9S7 6 7 3.5A3.5 3.5 0 0 0 3.5 0Z" fill="#fff"/><circle cx="3.5" cy="3.5" r="1.2" fill="#1a5ea6"/></svg><div>480 Harbor Lane<br>Suite 12<br>Westbrook, NJ 07000</div></div>
  <div class="row"><svg width="7" height="7" viewBox="0 0 7 7"><path d="M1 0L2.5 0L3 2L2 3Q3 4.5 4 5L5 4L7 4.5L7 6L6 7Q2 6.5 0 1Z" fill="#fff"/></svg><div>+1 (555) 014 2290</div></div>
  <div class="row"><svg width="8" height="7" viewBox="0 0 8 7"><rect x="2" y="0" width="4" height="2" fill="#fff"/><rect x="0" y="2.5" width="8" height="3" fill="#fff"/><rect x="2" y="5" width="4" height="2" fill="#fff"/></svg><div>123.456.7890</div></div>
  <div class="row"><svg width="7" height="6" viewBox="0 0 7 6"><rect width="7" height="5" fill="#fff"/><polyline points="0,0 3.5,3 7,0" fill="none" stroke="#1a5ea6" stroke-width=".8"/></svg><div>hello@beaconadvisoryinc.com</div></div>
</div>
<div class="abs divider" style="left:280px"></div>

<div class="abs f-col" style="left:306px">
  <h5>Quick Contact</h5>
  <div class="field">Name</div>
  <div class="field">Phone</div>
  <div class="field" style="height:34px">Message</div>
  <div class="submit">SUBMIT</div>
</div>
<div class="abs divider" style="left:474px"></div>

<div class="abs f-brand"><span class="brand-mark"></span><span class="brand-name">Beacon Advisory</span></div>
<div class="abs socials"><i></i><i></i><i></i><i style="background:#f19a1f"></i></div>

<div class="abs copyright">Copyright © 2016 Beaconadvisoryinc. All Rights Reserved.</div>

</body>
</html>
```